Professional and creative business card design for recruiting service providers

Our company supports German medium-sized companies in filling vacancies promptly. For this we use social media marketing and bring our customers into the visibility.

We want a professional but also creative design for our business cards.

Please look at lindqvar-staff.de to get an impression of our CI.

Target Market(s)

Small and medium-sized companies in Germany from the industry

Industry/Entity Type

Industrie, Handwerk

Contact Information for Business Card

Name, Position, Telefonnummer, Email, Website

Colors
EE7325
F08F49
F5BC92
FAE3D3
FDF4ED

Requirements
Must have
• A picture of the employee and in the style of www.lindqvar-staff.de

```html
<!DOCTYPE html>
<html lang="de">
<head>
<meta charset="utf-8">
<title>Lindqvar &amp; Staff – Visitenkarte</title>
<link rel="stylesheet" href="https://fonts.googleapis.com/css2?family=Montserrat:wght@700;800&family=Questrial&display=swap">
<style>
  :root {
    --stage: #2a2a2a;
    --ink: #111111;
    --paper: #ffffff;
    --orange: #ee5a24;
    --photo-tone-a: #dcdadc;
    --photo-tone-b: #3a3a44;
    --back-a: #1c1c1c;
    --back-b: #050505;
  }
  * { box-sizing: border-box; margin: 0; padding: 0; }
  html, body { width: 1200px; height: 1015px; overflow: hidden; }
  body {
    background: var(--stage);
    position: relative;
    font-family: "Questrial", "Century Gothic", sans-serif;
  }
  .card {
    position: absolute;
    left: 240px;
    width: 720px;
    height: 411px;
    overflow: hidden;
    box-shadow: 0 18px 40px rgba(0,0,0,.55);
  }

  /* ---------- Back side ---------- */
  .card--back { top: 56px; }
  .card--back .pattern-field {
    position: absolute; inset: 0;
    background: radial-gradient(ellipse at 70% 20%, var(--back-a), var(--back-b) 75%);
  }
  .card--back .brand {
    position: absolute;
    left: 50%; top: 50%;
    transform: translate(-50%, -50%);
    display: flex; align-items: center; gap: 18px;
  }
  .brand__square {
    width: 26px; height: 26px;
    background: var(--orange);
    flex: none;
  }
  .brand__name {
    font-family: "Montserrat", sans-serif;
    font-weight: 800;
    letter-spacing: .08em;
    line-height: 1.05;
    text-transform: uppercase;
  }
  .card--back .brand__name { color: var(--paper); font-size: 30px; }

  /* ---------- Front side ---------- */
  .card--front { top: 548px; background: var(--paper); }
  .card--front .brand {
    position: absolute; left: 62px; top: 112px;
    display: flex; align-items: center; gap: 16px;
  }
  .card--front .brand__square { width: 34px; height: 34px; }
  .card--front .brand__name { color: var(--ink); font-size: 30px; }

  .person { position: absolute; left: 62px; top: 218px; }
  .person__name {
    font-family: "Montserrat", sans-serif;
    font-weight: 700;
    font-size: 25px;
    letter-spacing: .02em;
    color: var(--ink);
    text-transform: uppercase;
  }
  .person__role {
    font-size: 17px;
    letter-spacing: .06em;
    color: var(--orange);
    text-transform: uppercase;
    margin-top: 2px;
  }
  .contacts { list-style: none; margin-top: 22px; }
  .contacts li {
    display: flex; align-items: center; gap: 12px;
    font-size: 19px; color: var(--ink);
    margin-bottom: 6px;
  }
  .contacts svg { width: 18px; height: 18px; flex: none; }

  .photo-frame {
    position: absolute;
    left: 420px; top: 44px;
    width: 262px; height: 300px;
    border: 3px solid var(--orange);
    background: var(--paper);
    z-index: 2;
  }
  .photo-frame .photo {
    position: absolute; inset: 0;
    background: linear-gradient(180deg, var(--photo-tone-a) 0%, var(--photo-tone-a) 45%, var(--photo-tone-b) 100%);
  }
  .band-dark {
    position: absolute; left: 0; bottom: 0;
    width: 440px; height: 9px;
    background: var(--ink);
  }
  .band-orange {
    position: absolute; left: 440px; right: 0; bottom: 0;
    height: 44px;
    background: var(--orange);
    z-index: 1;
  }
</style>
</head>
<body>

  <section class="card card--back" aria-label="Rückseite">
    <div class="pattern-field" role="img" aria-label="Dunkles Hintergrundmuster aus wiederholten Sechseck-Formen"></div>
    <div class="brand">
      <span class="brand__square"></span>
      <span class="brand__name">Lindqvar<br>&amp; Staff</span>
    </div>
  </section>

  <section class="card card--front" aria-label="Vorderseite">
    <div class="brand">
      <span class="brand__square"></span>
      <span class="brand__name">Lindqvar<br>&amp; Staff</span>
    </div>

    <div class="person">
      <p class="person__name">Jonas Berglund</p>
      <p class="person__role">Managing Director</p>
      <ul class="contacts">
        <li>
          <svg viewBox="0 0 24 24" aria-hidden="true"><path fill="var(--orange)" d="M6.6 10.8a15 15 0 0 0 6.6 6.6l2.2-2.2c.3-.3.7-.4 1-.2 1.1.4 2.3.6 3.6.6.6 0 1 .4 1 1V20c0 .6-.4 1-1 1A17 17 0 0 1 3 4c0-.6.4-1 1-1h3.5c.6 0 1 .4 1 1 0 1.3.2 2.5.6 3.6.1.3 0 .7-.2 1z"/></svg>
          044-987 650 321
        </li>
        <li>
          <svg viewBox="0 0 24 24" aria-hidden="true"><rect x="2" y="5" width="20" height="14" fill="var(--orange)"/><path d="M2 5l10 8 10-8" fill="none" stroke="#fff" stroke-width="1.6"/></svg>
          info@lindqvar-staff.de
        </li>
        <li>
          <svg viewBox="0 0 24 24" aria-hidden="true"><g fill="none" stroke="var(--orange)" stroke-width="1.8"><circle cx="12" cy="12" r="9.5"/><ellipse cx="12" cy="12" rx="4" ry="9.5"/><path d="M2.5 12h19M4 7h16M4 17h16"/></g></svg>
          www.lindqvar-staff.de
        </li>
      </ul>
    </div>

    <div class="photo-frame">
      <div class="photo" role="img" aria-label="Porträtfoto des Mitarbeiters vor hellgrauem Hintergrund"></div>
    </div>
    <div class="band-dark"></div>
    <div class="band-orange"></div>
  </section>

</body>
</html>
```